Brookvane Consulting Business Card Design

Business Card Design for Brookvane Consulting. Brookvane Consulting is a boutique consultancy based in Atlanta, GA., that specializes in marketing strategy, organization planning, and leadership development. We provide solutions for small businesses and startups as well as Vantage 300 companies.

http://brookvaneconsulting.com/

Target Market(s)

We provide solutions for small businesses and startups as well as Vantage 300 companies.

Industry/Entity Type

Consulting

Contact Information for Business Card

Two sided business card with priority on contact information, logo, tag line (Guidance to Plan Wider, Act Sooner, Grow Further)

Colors

Designer to choose colors to be used in the design.

Requirements
Must have
• contact information, logo, tag line (Guidance to Plan Wider, Act Sooner, Grow Further)
• Simple no over communication.
Nice to have
• I would like to see different placements of logo and creative use of both sides of the card
Should not have
• Do not put too much information on the card.

```html
<!DOCTYPE html>
<html lang="en">
<head>
<meta charset="UTF-8">
<title>Brookvane Consulting – Business Card</title>
<link rel="stylesheet" href="https://fonts.googleapis.com/css2?family=Montserrat:wght@400;600&family=Roboto:wght@400&display=swap">
<style>
  :root {
    --backdrop: #2b2b2b;
    --card: #353535;
    --ink: #ffffff;
    --ink-soft: #e6e6e6;
  }
  * { margin: 0; padding: 0; box-sizing: border-box; }
  html, body { width: 799px; height: 1200px; overflow: hidden; }
  body {
    background: var(--backdrop);
    position: relative;
    font-family: "Montserrat", sans-serif;
    color: var(--ink);
  }
  .card {
    position: absolute;
    left: 90px;
    width: 620px;
    height: 354px;
    background: var(--card);
    border-radius: 26px;
    box-shadow: 0 14px 30px rgba(0,0,0,0.45);
  }
  .card--front { top: 110px; }
  .card--back { top: 690px; }

  .wordmark {
    display: flex;
    align-items: center;
    gap: 12px;
    font-family: "Montserrat", sans-serif;
    font-weight: 600;
    color: var(--ink);
    white-space: nowrap;
  }
  .wordmark__square {
    width: 22px;
    height: 22px;
    background: var(--ink);
    flex: none;
  }
  .card--front .wordmark {
    position: absolute;
    left: 50%;
    top: 50%;
    transform: translate(-50%, -50%);
    font-size: 38px;
  }

  .card--back .brand {
    position: absolute;
    left: 40px;
    top: 44px;
  }
  .card--back .wordmark { font-size: 30px; }
  .card--back .wordmark__square { width: 18px; height: 18px; }
  .tagline {
    margin-top: 10px;
    font-size: 13px;
    font-weight: 400;
    letter-spacing: 0.3px;
    color: var(--ink-soft);
  }

  .contact {
    position: absolute;
    left: 300px;
    top: 200px;
    font-family: "Roboto", sans-serif;
  }
  .contact__name {
    font-family: "Montserrat", sans-serif;
    font-weight: 600;
    font-size: 22px;
    margin-bottom: 12px;
  }
  .contact__line {
    font-size: 16px;
    line-height: 22px;
    color: var(--ink-soft);
  }
</style>
</head>
<body>
  <section class="card card--front" aria-label="Card front">
    <div class="wordmark">
      <span class="wordmark__square"></span>
      <span>Brookvane Consulting</span>
    </div>
  </section>

  <section class="card card--back" aria-label="Card back">
    <div class="brand">
      <div class="wordmark">
        <span class="wordmark__square"></span>
        <span>Brookvane Consulting</span>
      </div>
      <p class="tagline">Guidance to Plan Wider, Act Sooner, Grow Further</p>
    </div>
    <div class="contact">
      <p class="contact__name">Tavin</p>
      <p class="contact__line">555-014-2287</p>
      <p class="contact__line">tavin@brookvaneconsulting.com</p>
      <p class="contact__line">www.brookvaneconsulting.com</p>
    </div>
  </section>
</body>
</html>
```